Looking to Redesign Brevonix.com website

You guys did one of the brochures for brevonix.com and I would like to see if we can go ahead and get an estimate for a redesigned web site for the company. We currently have a couple of pages on brevonix.com which are very much a starter type site.

The new design will need to reflect some of the things discussed in the brochure. It will have flash. Needs to be designed for simple hosting using cpanels.

The site needs to have between 12 and 15 pages with flash pages to move through features. Integrated with twitter like it is now, and contact forms delivered from our CRM along with other interactive features such as subscription to newsletter, etc...

I don't have lots of details on how to proceed yet, but here are some competitor sites:

Can we take a look at potential costs involved in the redo of the site as vague as my description above can permit.

Target Market(s)

Business to Business

Number of Pages Required

5+ page

Font styles to use
Sans Serif

Requirements
Must have
• Must have professional feel. Similar to brochure. and logo.
• Include our story in the discussion.
• embedded links to our CRM for popup contact forms.
• Logo files and 2 types of brochures uploaded.
• Important to keep color scheme
Nice to have
• Flash and some movement
Should not have
• Not sure yet

```html
<!DOCTYPE html>
<html lang="en">
<head>
<meta charset="utf-8">
<title>Brevonix – Universal Communication</title>
<link href="https://fonts.googleapis.com/css2?family=Open+Sans:wght@400;600;700&family=Roboto+Condensed:wght@400;700&display=swap" rel="stylesheet">
<style>
:root{
  --red:#c0161b;
  --red-deep:#a51217;
  --red-band:#b9262b;
  --ink:#333333;
  --muted:#666666;
  --nav:#3d3d3d;
  --nav-line:#2a2a2a;
  --dark:#161616;
  --footer-bar:#2b2b2b;
  --white:#ffffff;
  --line:#e4e4e4;
}
*{box-sizing:border-box;margin:0;padding:0}
html,body{width:1200px;height:3629px;overflow:hidden}
body{font-family:"Open Sans",Arial,sans-serif;color:var(--ink);background:var(--white);position:relative;font-size:13px;line-height:1.6}
.heading{font-family:"Roboto Condensed",Arial,sans-serif;font-weight:700;text-transform:uppercase}
ul{list-style:none}

/* header */
.site-header{position:absolute;top:0;left:0;width:1200px;height:135px}
.brand{position:absolute;left:98px;top:30px;display:flex;align-items:center;gap:12px}
.brand-dot{width:50px;height:50px;border-radius:50%;background:var(--red)}
.brand-name{font-family:"Roboto Condensed",Arial,sans-serif;font-weight:700;font-size:30px;color:var(--red)}
.social{position:absolute;left:757px;top:50px;display:flex;gap:5px}
.social span{width:19px;height:19px;border-radius:50%;background:#3b5998}
.social span:nth-child(2){background:#0e76a8}
.social span:nth-child(3){background:#2aa9e0}
.social span:nth-child(4){background:#d23f31}
.search{position:absolute;left:870px;top:48px;width:232px;height:24px;border:1px solid #ccc;font-size:10px;color:#555;padding:4px 8px}
.main-nav{position:absolute;left:97px;top:135px;width:1005px;height:53px;background:var(--nav);display:flex}
.main-nav a{display:flex;align-items:center;justify-content:center;padding:0 24px;color:var(--white);font-size:12px;font-weight:600;text-decoration:none;border-right:1px solid var(--nav-line);text-transform:uppercase}
.main-nav a.active{background:var(--red)}
.main-nav a:last-child{border-right:none;margin-left:auto}

/* hero */
.hero{position:absolute;top:188px;left:0;width:1200px;height:519px;background:linear-gradient(120deg,#9aa3aa 0%,#5d666d 40%,#3a4147 70%,#525a60 100%)}
.hero-photo{position:absolute;inset:0}
.hero-brand{position:absolute;left:650px;top:130px;display:flex;align-items:center;gap:10px}
.hero-brand .brand-dot{background:var(--white);width:56px;height:56px}
.hero-brand .brand-name{color:var(--white);font-size:34px}
.hero-title{position:absolute;left:642px;top:236px;width:500px;color:var(--white);font-size:34px;line-height:1.15;font-family:"Open Sans",Arial,sans-serif;font-weight:600}
.hero-text{position:absolute;left:642px;top:326px;width:520px;color:#f0f0f0;font-size:14px;line-height:1.55}
.hero-arrow{position:absolute;top:245px;width:30px;height:30px;border-radius:50%;background:rgba(255,255,255,.25)}
.hero-arrow.prev{left:34px}.hero-arrow.next{left:1138px}

/* welcome */
.welcome{position:absolute;top:707px;left:0;width:1200px;height:464px}
.diagram{position:absolute;left:107px;top:70px;width:305px;height:318px;border:2px solid #e79b9d;background:#f7f7f7}
.welcome-body{position:absolute;left:553px;top:90px;width:550px}
.section-title{font-size:32px;color:var(--ink);line-height:1.1}
.section-title em{font-style:normal;color:var(--red)}
.welcome-body p{font-size:11.5px;color:var(--muted);margin-top:14px;line-height:1.75}
.welcome-body h3{font-weight:400;font-size:16px;color:#555;margin-top:18px}

/* why */
.why{position:absolute;top:1171px;left:0;width:1200px;height:489px;background:var(--red-band);color:var(--white)}
.why-body{position:absolute;left:123px;top:85px;width:450px}
.why-body .section-title{color:var(--white)}
.why-body h4{font-size:13px;font-weight:600;margin-top:16px}
.why-body p{font-size:10.5px;margin-top:10px;line-height:1.7}
.ticks{margin-top:14px}
.ticks li{display:flex;align-items:center;gap:10px;font-size:11.5px;margin-bottom:9px}
.ticks svg{flex:none}
.why-photo{position:absolute;left:630px;top:70px;width:440px;height:350px;border:8px solid var(--white);background:linear-gradient(135deg,#d9e4ea,#8fb0c4 60%,#5e7f95)}

/* features */
.features{position:absolute;top:1660px;left:0;width:1200px;height:640px}
.centered-title{position:absolute;left:0;width:1200px;text-align:center;font-family:"Roboto Condensed",Arial,sans-serif;font-weight:400;font-size:32px;color:var(--ink);text-transform:uppercase}
.features .centered-title{top:70px}
.subtitle{position:absolute;top:122px;left:0;width:1200px;text-align:center;font-size:15px;color:#555}
.feature{position:absolute;width:340px;height:160px}
.feature-icon{position:absolute;left:0;top:0;width:80px;height:80px;border-radius:50%;background:var(--red);display:flex;align-items:center;justify-content:center}
.feature-body{position:absolute;left:100px;top:0;width:235px}
.feature-body h3{font-size:14px;font-weight:400;color:#444}
.feature-body hr{border:none;height:2px;width:55px;background:var(--red);margin:9px 0 10px}
.feature-body p{font-size:10.5px;color:var(--muted);line-height:1.6}
.feature-body .more{font-size:11px;color:#888;margin-top:10px}

/* advantages */
.advantages{position:absolute;top:2300px;left:0;width:1200px;height:490px;background:radial-gradient(ellipse at 30% 50%,#2c1a1a,var(--dark) 70%)}
.adv-photo{position:absolute;left:150px;top:85px;width:440px;height:295px;border:8px solid var(--white);background:linear-gradient(135deg,#cfe3f3,#6d97c2 55%,#244b78)}
.adv-body{position:absolute;left:630px;top:100px;width:470px;color:var(--white)}
.adv-body .section-title{color:var(--white)}
.adv-body h4{font-size:13px;font-weight:600;margin-top:12px}
.adv-body p{font-size:10.5px;margin-top:12px;line-height:1.7}

/* blog */
.blog{position:absolute;top:2790px;left:0;width:1200px;height:490px}
.blog .centered-title{top:40px}
.post{position:absolute;top:143px;width:310px}
.post-photo{width:310px;height:177px}
.post-meta{margin-top:20px;font-size:12px;color:var(--red);font-weight:600}
.post p{font-size:10.5px;color:var(--muted);margin-top:4px;line-height:1.6}

/* footer */
.site-footer{position:absolute;top:3280px;left:0;width:1200px;height:297px;background:var(--red);color:var(--white)}
.footer-col{position:absolute;top:52px}
.footer-col h3{font-size:15px;font-weight:400;text-transform:uppercase;font-family:"Open Sans",Arial,sans-serif}
.footer-col hr{border:none;height:1px;width:40px;background:rgba(255,255,255,.6);margin:7px 0 12px}
.footer-col p,.footer-col li{font-size:11px;line-height:1.6}
.contact-line{display:flex;gap:12px;margin-top:14px;align-items:flex-start}
.tweet{display:flex;gap:10px;margin-bottom:12px}
.tweet .bird{width:16px;height:16px;background:var(--white);flex:none;border-radius:2px}
.tweet small{display:block;font-size:10px;opacity:.85;margin-top:4px}
.news-input{width:242px;height:40px;background:var(--white);color:#555;font-size:10px;padding:12px 10px;margin-top:14px}
.news-row{display:flex;align-items:center;gap:8px;margin-top:20px}
.subscribe{background:#2d2d2d;font-size:11px;padding:8px 12px;text-transform:uppercase}
.news-row span.dot{width:22px;height:22px;border-radius:50%;background:var(--white)}
.quick-links li{text-transform:uppercase;font-size:11px;line-height:1.6}
.footer-bar{position:absolute;top:3577px;left:0;width:1200px;height:52px;background:var(--footer-bar);color:#ccc;font-size:11px;text-align:center;line-height:52px}
</style>
</head>
<body>

<header class="site-header">
  <div class="brand"><span class="brand-dot"></span><span class="brand-name">Brevonix</span></div>
  <div class="social"><span></span><span></span><span></span><span></span></div>
  <div class="search">SEARCH</div>
</header>
<nav class="main-nav">
  <a class="active">Home</a><a>About Us</a><a>Why Brevonix</a><a>Features</a><a>Advantages</a><a>Best of Class Hardware</a><a>Contact Us</a>
</nav>

<section class="hero">
  <div class="hero-photo" role="img" aria-label="Man in a grey sweater holding a glowing light bulb on a string against a stormy sky"></div>
  <div class="hero-brand"><span class="brand-dot"></span><span class="brand-name">Brevonix</span></div>
  <h1 class="hero-title">BREVONIX UNIVERSAL COMMUNICATION</h1>
  <p class="hero-text">Nemo enim ipsam voluptatem quia voluptas sit aspernatur aut odit aut fugit, sed quia consequuntur magni dolores eos</p>
  <span class="hero-arrow prev"></span><span class="hero-arrow next"></span>
</section>

<section class="welcome">
  <div class="diagram" role="img" aria-label="Network diagram of client sites connected to unified communication and redundant telephony providers"></div>
  <div class="welcome-body">
    <h2 class="section-title heading">Welcome to <em>Brevonix</em></h2>
    <p>Brevonix has been in the business of providing hosted based PBX services since early 2003. This is before most of the business world had ever heard of such a service. Yes, you may have never heard of us or our services. Fact is we have been providing services to corporate clients as a part of an IT managed services group and were not marketing to other businesses.</p>
    <h3>So what is different now?</h3>
    <p>We have acquired a traditional services provider and we got spun off into our own entity. Now we are able to bring to the general market these unique services. Your solution will be completely custom to you, redundant, secure, reliable, and above all simple to use, access, and modify.</p>
  </div>
</section>

<section class="why">
  <div class="why-body">
    <h2 class="section-title heading">Why Brevonix</h2>
    <h4>Brevonix Universal Communication</h4>
    <p>Fax, Phone, Wireless, Email, Text Messaging, Web, Cellular, and Integrated Backoffice Systems. In addition to being costly, traditional communication systems tend to operate in isolated modes leaving little room for easy integration.</p>
    <ul class="ticks">
      <li><svg width="12" height="12" viewBox="0 0 12 12"><path d="M1 6.5l3 3 7-7" stroke="#fff" stroke-width="2" fill="none"/></svg>Define their own requirements based on their style and needs.</li>
      <li><svg width="12" height="12" viewBox="0 0 12 12"><path d="M1 6.5l3 3 7-7" stroke="#fff" stroke-width="2" fill="none"/></svg>Seamlessly integrate many locations into a unified infrastructure.</li>
      <li><svg width="12" height="12" viewBox="0 0 12 12"><path d="M1 6.5l3 3 7-7" stroke="#fff" stroke-width="2" fill="none"/></svg>Integrate a wide array of special features as well as defined feature sets.</li>
      <li><svg width="12" height="12" viewBox="0 0 12 12"><path d="M1 6.5l3 3 7-7" stroke="#fff" stroke-width="2" fill="none"/></svg>Simplify people's movement and telecommuting.</li>
      <li><svg width="12" height="12" viewBox="0 0 12 12"><path d="M1 6.5l3 3 7-7" stroke="#fff" stroke-width="2" fill="none"/></svg>Incorporate email, pagers, cellular phones, and other devices.</li>
    </ul>
  </div>
  <div class="why-photo" role="img" aria-label="Two colleagues smiling while working at a laptop in a bright office"></div>
</section>

<section class="features">
  <h2 class="centered-title">Our Features</h2>
  <p class="subtitle">Unified Communications Sample of Powerful Feature Sets</p>

  <article class="feature" style="left:97px;top:230px">
    <div class="feature-icon"><svg width="38" height="38" viewBox="0 0 38 38" fill="none" stroke="#fff" stroke-width="3"><path d="M6 24v-5a13 13 0 0126 0v5"/><rect x="4" y="22" width="7" height="11" rx="2" fill="#fff"/><rect x="27" y="22" width="7" height="11" rx="2" fill="#fff"/></svg></div>
    <div class="feature-body"><h3>Outgoing Call Redundancies</h3><hr><p>Multiple Telecommunications Providers create excellent service redundancies for outgoing calls. If a provider</p><div class="more">Read More ›</div></div>
  </article>
  <article class="feature" style="left:452px;top:230px">
    <div class="feature-icon"><svg width="34" height="34" viewBox="0 0 24 24" fill="#fff"><path d="M6.6 10.8a15 15 0 006.6 6.6l2.2-2.2a1 1 0 011-.25 11.4 11.4 0 003.6.6 1 1 0 011 1V20a1 1 0 01-1 1A17 17 0 013 4a1 1 0 011-1h3.5a1 1 0 011 1c0 1.25.2 2.45.6 3.6a1 1 0 01-.25 1z"/></svg></div>
    <div class="feature-body"><h3>Incoming Call Redundancies</h3><hr><p>Multiple Telecommunications Providers provide excellent redundancies for incoming calls. We can split your</p><div class="more">Read More ›</div></div>
  </article>
  <article class="feature" style="left:799px;top:230px">
    <div class="feature-icon"><svg width="40" height="34" viewBox="0 0 40 34" fill="none" stroke="#fff" stroke-width="3.5" stroke-linecap="round"><path d="M3 12a24 24 0 0134 0"/><path d="M9 18a15 15 0 0122 0"/><path d="M15 24a7 7 0 0110 0"/><circle cx="20" cy="29" r="2" fill="#fff"/></svg></div>
    <div class="feature-body"><h3>Implementation Ease</h3><hr><p>We can use the same key combinations as an existing system if a client wishes to maintain a similar feel to their</p><div class="more">Read More ›</div></div>
  </article>
  <article class="feature" style="left:97px;top:420px">
    <div class="feature-icon"><svg width="38" height="34" viewBox="0 0 38 34" fill="#fff"><path d="M4 3h22a3 3 0 013 3v12a3 3 0 01-3 3H13l-7 6v-6H4a3 3 0 01-3-3V6a3 3 0 013-3z"/><path d="M31 10h3a3 3 0 013 3v10a3 3 0 01-3 3h-1v5l-6-5H16l3-3h12z"/></svg></div>
    <div class="feature-body"><h3>911 Notification</h3><hr><p>Allows designated client personnel to be automatically notified when a call to emergency services is initiated.</p><div class="more">Read More ›</div></div>
  </article>
  <article class="feature" style="left:452px;top:420px">
    <div class="feature-icon"><svg width="38" height="28" viewBox="0 0 38 28" fill="none" stroke="#fff" stroke-width="3"><rect x="2" y="2" width="34" height="24" rx="2"/><path d="M2 4l17 13L36 4"/></svg></div>
    <div class="feature-body"><h3>Advanced Voicemail</h3><hr><p>capabilities including Voice2Email, email notification, pager notification, cellular and other device delivery.</p><div class="more">Read More ›</div></div>
  </article>
  <article class="feature" style="left:799px;top:420px">
    <div class="feature-icon"><svg width="38" height="38" viewBox="0 0 38 38" fill="none" stroke="#fff" stroke-width="4"><circle cx="14" cy="20" r="7"/><path d="M14 8v4M14 28v4M2 20h4M22 20h4M5.5 11.5l3 3M19.5 25.5l3 3M5.5 28.5l3-3M19.5 14.5l3-3" stroke-width="3"/><circle cx="29" cy="9" r="4" stroke-width="3"/></svg></div>
    <div class="feature-body"><h3>Automated Response</h3><hr><p>Allows customized response by hour of day, day of week, as well as emergency and other forwarding features.</p><div class="more">Read More ›</div></div>
  </article>
</section>

<section class="advantages">
  <div class="adv-photo" role="img" aria-label="Hand typing on a laptop with glowing digital network graphics"></div>
  <div class="adv-body">
    <h2 class="section-title heading">Advantages</h2>
    <h4>Brevonix Managed Telephony - Cost Comparison</h4>
    <p>Traditional systems are costly. Companies in the market for replacement or upgrades are discovering that in addition to the initial purchase price, the total cost of ownership includes:</p>
    <ul class="ticks">
      <li><svg width="12" height="12" viewBox="0 0 12 12"><path d="M1 6.5l3 3 7-7" stroke="#fff" stroke-width="2" fill="none"/></svg>Initial purchase price</li>
      <li><svg width="12" height="12" viewBox="0 0 12 12"><path d="M1 6.5l3 3 7-7" stroke="#fff" stroke-width="2" fill="none"/></svg>since not all features are included, there is a cost to activate features</li>
      <li><svg width="12" height="12" viewBox="0 0 12 12"><path d="M1 6.5l3 3 7-7" stroke="#fff" stroke-width="2" fill="none"/></svg>monthly maintenance fees (basic and based on activated features)</li>
      <li><svg width="12" height="12" viewBox="0 0 12 12"><path d="M1 6.5l3 3 7-7" stroke="#fff" stroke-width="2" fill="none"/></svg>reprogramming and other adjustments</li>
      <li><svg width="12" height="12" viewBox="0 0 12 12"><path d="M1 6.5l3 3 7-7" stroke="#fff" stroke-width="2" fill="none"/></svg>on-site billable work above and beyond monthly maintenance</li>
    </ul>
  </div>
</section>

<section class="blog">
  <h2 class="centered-title">Latest Blog</h2>
  <article class="post" style="left:97px">
    <div class="post-photo" role="img" aria-label="Office team gathered around a laptop" style="background:linear-gradient(135deg,#e6e3de,#b9aea3 60%,#7d6f64)"></div>
    <div class="post-meta">JAN 27, 2016 &nbsp;\&nbsp; 2 COMMENTS</div>
    <p>Lorem ipsum dolor sit amet, consectetur adipiscing elit. Sed blandit massa vel mauris sollicitudin dignissim. Lorem ipsum dolor sit amet, consectetur</p>
  </article>
  <article class="post" style="left:445px">
    <div class="post-photo" role="img" aria-label="Business people in a conference room" style="background:linear-gradient(135deg,#b7a690,#6b5a48 60%,#3c3128)"></div>
    <div class="post-meta">JAN 21, 2016 &nbsp;\&nbsp; 2 COMMENTS</div>
    <p>Lorem ipsum dolor sit amet, consectetur adipiscing elit. Sed blandit massa vel mauris sollicitudin dignissim. Lorem ipsum dolor sit amet, consectetur</p>
  </article>
  <article class="post" style="left:794px">
    <div class="post-photo" role="img" aria-label="Businessman touching a glowing digital interface" style="background:linear-gradient(135deg,#9fc3dc,#3d6e94 55%,#16324d)"></div>
    <div class="post-meta">JAN 21, 2016 &nbsp;\&nbsp; 2 COMMENTS</div>
    <p>Lorem ipsum dolor sit amet, consectetur adipiscing elit. Sed blandit massa vel mauris sollicitudin dignissim. Lorem ipsum dolor sit amet, consectetur</p>
  </article>
</section>

<footer class="site-footer">
  <div class="footer-col" style="left:97px;width:260px">
    <h3>Contact Us</h3><hr>
    <p>Call today and let us discover the truly best communication solution for you.</p>
    <div class="contact-line"><svg width="14" height="18" viewBox="0 0 14 18" fill="#fff"><path d="M7 0a7 7 0 017 7c0 5-7 11-7 11S0 12 0 7a7 7 0 017-7zm0 4a3 3 0 100 6 3 3 0 000-6z"/></svg><p>1820 Harbor Point Dr, Suite 410<br>Tampa, FL 33602</p></div>
    <div class="contact-line"><svg width="15" height="15" viewBox="0 0 24 24" fill="#fff"><path d="M6.6 10.8a15 15 0 006.6 6.6l2.2-2.2a1 1 0 011-.25 11.4 11.4 0 003.6.6 1 1 0 011 1V20a1 1 0 01-1 1A17 17 0 013 4a1 1 0 011-1h3.5a1 1 0 011 1c0 1.25.2 2.45.6 3.6a1 1 0 01-.25 1z"/></svg><p>Phone:+1 555 014 2290</p></div>
    <div class="contact-line"><svg width="15" height="12" viewBox="0 0 15 12" fill="none" stroke="#fff" stroke-width="1.5"><rect x="1" y="1" width="13" height="10"/><path d="M1 1l6.5 5L14 1"/></svg><p>sales@brevonix.com</p></div>
  </div>
  <div class="footer-col" style="left:418px;width:240px">
    <h3>Latest Tweet`s</h3><hr>
    <div class="tweet"><span class="bird"></span><p><b>@Brevonix</b> iusct varius mi. Cum sociis natoque penatibus et<small>1 day ago</small></p></div>
    <div class="tweet"><span class="bird"></span><p><b>@Brevonix</b> iusct varius mi. Cum sociis natoque penatibus et<small>1 day ago</small></p></div>
  </div>
  <div class="footer-col" style="left:694px;width:270px">
    <h3>Join Our Newsletter</h3><hr>
    <p>Excepteur sint occaecat cupidatat non proident, sunt in culpa qui</p>
    <div class="news-input">Enter Name</div>
    <div class="news-row"><span class="subscribe">Subscribe</span><span class="dot"></span><span class="dot"></span><span class="dot"></span><span class="dot"></span></div>
  </div>
  <div class="footer-col" style="left:998px;width:140px">
    <h3>Quick Links</h3><hr>
    <ul class="quick-links"><li>Home</li><li>About</li><li>Why Brevonix</li><li>Features</li><li>Advantages</li><li>Best of Class</li></ul>
  </div>
</footer>
<div class="footer-bar">Copyright 2016 | All Rights Reserved – Brevonix</div>

</body>
</html>
```